New stationary design for online film company

We need some new stationary to fit with our new logo. The stationary should be professional, clean and simple.
We need designs for a full set of business stationary.
We need - letterhead, envelopes, invoices, proposals, coverslip/note and cover page

Industry/Entity Type

Business

```html
<!DOCTYPE html>
<html lang="en">
<head>
<meta charset="utf-8">
<title>Lumacast Stationery Set</title>
<link href="https://fonts.googleapis.com/css2?family=Source+Sans+3:wght@400;600&display=swap" rel="stylesheet">
<style>
  :root {
    --navy: #0f4a72;
    --sky: #6aa6c1;
    --mist: #e3e3ec;
    --paper: #ffffff;
    --ink: #3a3f45;
    --backdrop: #e8e5e1;
    --edge: #1d1d1d;
  }
  * { box-sizing: border-box; margin: 0; padding: 0; }
  html, body { width: 1200px; height: 766px; overflow: hidden; }
  body {
    background: var(--backdrop);
    font-family: "Source Sans 3", "Myriad Pro", Arial, sans-serif;
    color: var(--ink);
    position: relative;
  }
  .sheet { position: absolute; background: var(--paper); box-shadow: 0 1px 4px rgba(0,0,0,.18); }
  .brand { font-weight: 600; color: var(--navy); line-height: 1; letter-spacing: -0.5px; white-space: nowrap; }
  .brand-row { display: flex; align-items: center; gap: 6px; }
  .brand-dot { border-radius: 50%; border: 3px solid var(--navy); flex: none; }
  .mark-circle { position: absolute; border-radius: 50%; }

  /* Letterhead */
  .letterhead { left: 14px; top: 16px; width: 525px; height: 742px; }
  .letterhead .brand-row { position: absolute; left: 28px; top: 32px; }
  .letterhead .brand { font-size: 30px; }
  .letterhead .brand-dot { width: 26px; height: 26px; }
  .letterhead .contact {
    position: absolute; left: 402px; top: 18px; padding-left: 8px;
    border-left: 1px solid #c9cdd2; font-size: 9.5px; line-height: 14.5px;
  }
  .contact li { list-style: none; display: flex; align-items: center; gap: 5px; }
  .contact svg { width: 8px; height: 8px; flex: none; }
  .letterhead .watermark { left: 142px; top: 264px; width: 240px; height: 240px; border: 20px solid var(--mist); }
  .letterhead .footer-address {
    position: absolute; left: 0; right: 0; top: 724px; text-align: center;
    font-size: 8.5px; letter-spacing: 0.8px;
  }

  /* Business cards */
  .card-front { left: 566px; top: 16px; width: 223px; height: 126px; }
  .card-front .brand-row { position: absolute; left: 26px; top: 46px; }
  .card-front .brand { font-size: 27px; }
  .card-front .brand-dot { width: 24px; height: 24px; }
  .card-front .card-web {
    position: absolute; left: 0; right: 0; top: 112px; text-align: center;
    font-size: 5.5px; letter-spacing: 1.6px; font-weight: 600;
  }
  .card-back { left: 802px; top: 18px; width: 222px; height: 126px; }
  .card-back .badge { left: 20px; top: 38px; width: 68px; height: 68px; border: 8px solid var(--navy); }
  .card-back .details { position: absolute; left: 119px; top: 14px; font-size: 5.5px; line-height: 7.5px; }
  .card-back .brand { font-size: 18px; margin-bottom: 8px; }
  .card-back .person { font-size: 8px; font-weight: 600; color: var(--navy); line-height: 9px; }
  .card-back .role { font-size: 6px; color: var(--sky); margin-bottom: 7px; }
  .card-back .contact svg { width: 5px; height: 5px; }
  .card-back .contact li { gap: 3px; line-height: 10px; }
  .card-back .address { margin-top: 4px; }

  /* Envelopes */
  .envelope { position: absolute; background: var(--paper); }
  .envelope svg.flap { position: absolute; left: 0; top: 0; }
  .env-sky { left: 566px; top: 160px; width: 603px; height: 90px; }
  .env-navy { left: 566px; top: 242px; width: 603px; height: 387px; box-shadow: 0 1px 4px rgba(0,0,0,.15); }
  .env-outline { left: 554px; top: 359px; width: 604px; height: 270px; border: 1px solid var(--edge); border-top: none; }
  .env-front { left: 571px; top: 478px; width: 605px; height: 270px; box-shadow: 0 1px 5px rgba(0,0,0,.2); }
  .env-front .brand-row { position: absolute; left: 31px; top: 16px; }
  .env-front .brand { font-size: 28px; }
  .env-front .brand-dot { width: 24px; height: 24px; }
  .env-front .return-address { position: absolute; left: 31px; top: 70px; font-size: 9px; letter-spacing: 0.8px; }
  .env-front .env-web { position: absolute; left: 31px; top: 244px; font-size: 8px; letter-spacing: 2px; font-weight: 600; }
  .env-front .watermark { left: 528px; top: 193px; width: 52px; height: 52px; border: 5px solid var(--mist); }
</style>
</head>
<body>

<!-- Letterhead -->
<section class="sheet letterhead">
  <div class="brand-row"><span class="brand-dot"></span><span class="brand">Lumacast</span></div>
  <ul class="contact">
    <li><svg viewBox="0 0 10 10"><circle cx="5" cy="5" r="4.3" fill="none" stroke="#555" stroke-width="1"/><path d="M3.5 3 q0 3.5 3 4" fill="none" stroke="#555" stroke-width="1.2"/></svg>123-456-7890</li>
    <li><svg viewBox="0 0 10 10"><rect x="0.8" y="2" width="8.4" height="6" fill="none" stroke="#555" stroke-width="1"/><path d="M1 2.3 5 5.5 9 2.3" fill="none" stroke="#555" stroke-width="1"/></svg>hello@lumacast.com</li>
    <li><svg viewBox="0 0 10 10"><circle cx="5" cy="5" r="4.3" fill="none" stroke="#555" stroke-width="1"/><ellipse cx="5" cy="5" rx="1.8" ry="4.3" fill="none" stroke="#555" stroke-width=".8"/><path d="M0.7 5h8.6" stroke="#555" stroke-width=".8"/></svg>www.lumacast.com</li>
  </ul>
  <div class="mark-circle watermark"></div>
  <p class="footer-address">00, Complex Name, street, city 000452</p>
</section>

<!-- Business card, front -->
<section class="sheet card-front">
  <div class="brand-row"><span class="brand-dot"></span><span class="brand">Lumacast</span></div>
  <p class="card-web">www.lumacast.com</p>
</section>

<!-- Business card, back -->
<section class="sheet card-back">
  <div class="mark-circle badge"></div>
  <div class="details">
    <p class="brand">Lumacast</p>
    <p class="person">Your Name</p>
    <p class="role">Designation</p>
    <ul class="contact">
      <li><svg viewBox="0 0 10 10"><circle cx="5" cy="5" r="4.3" fill="none" stroke="#555" stroke-width="1.2"/></svg>123-456-7890</li>
      <li><svg viewBox="0 0 10 10"><rect x="2.5" y="0.5" width="5" height="9" rx="1" fill="#555"/></svg>123-456-7890</li>
      <li><svg viewBox="0 0 10 10"><rect x="0.8" y="2" width="8.4" height="6" fill="#555"/></svg>hello@lumacast.com</li>
    </ul>
    <p class="address">00, Complex Name<br>street, city 000452</p>
  </div>
</section>

<!-- Envelope with light flap -->
<div class="envelope env-sky">
  <svg class="flap" width="603" height="90" viewBox="0 0 603 90">
    <path d="M0 0H603L597 40Q590 56 560 62L301 100L43 62Q13 56 6 40Z" fill="var(--sky)"/>
    <circle cx="301" cy="45" r="17" fill="none" stroke="#fff" stroke-width="4"/>
  </svg>
</div>

<!-- Envelope with dark flap -->
<div class="envelope env-navy">
  <svg class="flap" width="603" height="110" viewBox="0 0 603 110">
    <path d="M0 0H603L598 30Q592 52 560 59L314 104Q301 107 289 104L43 59Q12 52 6 30Z" fill="var(--navy)"/>
    <circle cx="301" cy="57" r="17" fill="none" stroke="#fff" stroke-width="4"/>
  </svg>
</div>

<!-- Envelope with outlined flap -->
<div class="envelope env-outline">
  <svg class="flap" width="604" height="112" viewBox="0 0 604 112">
    <path d="M0.5 0.5H603.5L598 28Q593 46 565 52L316 104Q302 108 288 104L42 54Q14 48 8 28Z" fill="#fff" stroke="var(--edge)" stroke-width="1"/>
    <circle cx="302" cy="55" r="17" fill="none" stroke="var(--navy)" stroke-width="5"/>
  </svg>
</div>

<!-- Envelope front -->
<section class="envelope env-front">
  <div class="brand-row"><span class="brand-dot"></span><span class="brand">Lumacast</span></div>
  <p class="return-address">00, Complex Name, street, city 000452</p>
  <div class="mark-circle watermark"></div>
  <p class="env-web">www.lumacast.com</p>
</section>

</body>
</html>
```